VFX Company Business Card Design Project

The Kestrel Works is a decentralized Visual Effects Studio servicing the television and feature film industries.
Project Brief:
Take our logo that was previously designed on Pencil Harbor and make a double sided business card.
Requirements:
- Card MUST be double sided.
- Front of card MUST have the yellow part of our logo against the dark grey background.
- Back of card is completely up to the designer.
- Back of card must include the complete company logo.
Please follow these File Preparation guidelines:
http://printnook.ca/infopage?file=filetype_en&s=PrintNook_new&lang=en
Business

```html
<!DOCTYPE html>
<html lang="en">
<head>
<meta charset="utf-8">
<title>The Kestrel Works – Business Card</title>
<link rel="stylesheet" href="https://fonts.googleapis.com/css2?family=Questrial&family=PT+Sans&display=swap">
<style>
  :root {
    --backdrop: #d3ab84;
    --card: #2b2b2b;
    --slate: #5e6b70;
    --cream: #eef3e6;
    --yellow: #f9c623;
    --light: #e4e4e4;
    --mark-grey: #a3adb1;
    --label: #1b1b1b;
  }
  * { margin: 0; padding: 0; box-sizing: border-box; }
  html, body { width: 1200px; height: 788px; overflow: hidden; }
  body {
    position: relative;
    background: var(--backdrop);
    font-family: "Questrial", sans-serif;
  }
  .view-label {
    position: absolute;
    width: 300px;
    text-align: center;
    font-family: "PT Sans", sans-serif;
    font-size: 22px;
    color: var(--label);
  }
  .label-back { left: 450px; top: 32px; }
  .label-front-1 { left: 166px; top: 403px; }
  .label-front-2 { left: 734px; top: 403px; }

  .card {
    position: absolute;
    width: 524px;
    height: 300px;
    border-radius: 22px;
    background: var(--card);
    overflow: hidden;
    color: var(--light);
  }
  .card-back { left: 338px; top: 78px; }
  .card-front-1 { left: 54px; top: 445px; }
  .card-front-2 { left: 622px; top: 445px; }

  .back-swoosh { position: absolute; inset: 0; }

  .back-name {
    position: absolute;
    left: 24px;
    top: 44px;
    font-size: 34px;
    color: var(--mark-grey);
  }
  .holder {
    position: absolute;
    left: 24px;
    top: 136px;
    font-size: 20px;
    color: var(--light);
  }
  .holder small { font-size: 14px; letter-spacing: 0.5px; }
  .contacts {
    position: absolute;
    left: 24px;
    top: 170px;
    list-style: none;
    font-size: 13.5px;
    line-height: 18px;
  }
  .contacts b { font-style: italic; font-weight: bold; display: inline-block; width: 20px; }
  .contacts .indent { padding-left: 22px; display: block; }

  .front-1-name {
    position: absolute;
    left: 0; right: 0;
    top: 118px;
    text-align: center;
    font-size: 48px;
    color: var(--yellow);
  }
  .front-2-mark {
    position: absolute;
    left: 0; right: 0;
    top: 124px;
    display: flex;
    align-items: center;
    justify-content: center;
    gap: 16px;
  }
  .mark-dot {
    width: 40px; height: 40px;
    border-radius: 50%;
    background: var(--yellow);
  }
  .front-2-name { font-size: 36px; color: var(--mark-grey); }

  .card-url {
    position: absolute;
    left: 0; right: 0;
    top: 257px;
    text-align: center;
    font-size: 20px;
    letter-spacing: 3px;
    color: #f2f2f2;
  }
</style>
</head>
<body>
  <div class="view-label label-back">Back</div>
  <div class="view-label label-front-1">Front - 1</div>
  <div class="view-label label-front-2">Front - 2</div>

  <section class="card card-back">
    <svg class="back-swoosh" width="524" height="300" viewBox="0 0 524 300" aria-hidden="true">
      <path d="M420,0 C470,30 500,100 490,170 C480,230 450,280 410,300 L524,300 L524,0 Z" fill="var(--slate)"/>
      <path d="M285,300 C380,282 462,232 478,110 C486,190 462,262 420,300 Z" fill="var(--cream)"/>
      <path d="M420,300 C462,262 486,190 478,110 C494,180 474,262 434,300 Z" fill="var(--card)"/>
    </svg>
    <div class="back-name">The Kestrel Works</div>
    <p class="holder">Your Name, <small>Designation</small></p>
    <ul class="contacts">
      <li><b>c :</b>123-456-7890</li>
      <li><b>p :</b>123-456-7890</li>
      <li><b>e :</b>info@kestrelworks.com</li>
      <li><b>w :</b>www.kestrelworks.com</li>
      <li><b>a :</b>0000#, Area Name<span class="indent">State Name, Country code</span></li>
    </ul>
  </section>

  <section class="card card-front-1">
    <div class="front-1-name">The Kestrel Works</div>
    <div class="card-url">www.kestrelworks.com</div>
  </section>

  <section class="card card-front-2">
    <div class="front-2-mark">
      <span class="mark-dot"></span>
      <span class="front-2-name">The Kestrel Works</span>
    </div>
    <div class="card-url">www.kestrelworks.com</div>
  </section>
</body>
</html>
```